Design 4 pages for an event discovery website

This is a contest for the design of 4 pages for an events discovery website. The feature is part of the new sign-up process.

Please see the attached document for a full scope, mockups and the parent category icons.

Target Market(s)

18-35 Australian event goers

Industry/Entity Type

Events

Number of Pages Required

4 page

```html
<!DOCTYPE html>
<html lang="en">
<head>
<meta charset="utf-8">
<title>VENUEO – Sign up, step 1 of 5</title>
<link rel="stylesheet" href="https://fonts.googleapis.com/css2?family=Open+Sans:wght@300;400;600;700&display=swap">
<style>
  :root {
    --page-bg: #eff0f5;
    --header-bg: #ffffff;
    --ink-dark: #4d4f55;
    --ink-body: #67686d;
    --accent-blue: #3aa3c9;
    --accent-orange: #f0924a;
    --search-yellow: #f5c533;
    --search-border: #e2e2e2;
    --signup-blue: #41a8cb;
    --login-green: #89ad5c;
    --chirply-blue: #3dbdeb;
    --pictora-brown: #a8662b;
    --tunewave-green: #8db13a;
    --songbox-red: #d93838;
    --note-green: #8caf3c;
    --note-red: #d94545;
    --footer-bg: #444444;
    --footer-ink: #dcdcdc;
    --white: #ffffff;
  }
  * { box-sizing: border-box; margin: 0; padding: 0; }
  html, body { width: 1200px; height: 664px; overflow: hidden; }
  body {
    position: relative;
    background: var(--page-bg);
    font-family: "Open Sans", Arial, sans-serif;
    color: var(--ink-body);
  }

  /* Header */
  .site-header {
    position: absolute; left: 0; top: 0; width: 1200px; height: 133px;
    background: var(--header-bg);
    box-shadow: 0 1px 3px rgba(0,0,0,0.35);
  }
  .brand {
    position: absolute; left: 99px; top: 48px;
    font-size: 27px; font-weight: 700; letter-spacing: 0.5px;
    color: var(--ink-dark);
  }
  .search {
    position: absolute; left: 600px; top: 50px; width: 274px; height: 34px;
    border: 1px solid var(--search-border); border-radius: 3px; background: var(--white);
  }
  .search-field {
    position: absolute; left: 9px; top: 7px; width: 254px; height: 18px;
    border-radius: 9px; background: linear-gradient(#f8d24a, #f1bb24);
    border: 1px solid #e0a91c;
    font-size: 10px; font-weight: 700; color: var(--white);
    padding-left: 10px; line-height: 16px;
  }
  .search-field svg { position: absolute; right: 8px; top: 3px; }
  .header-btn {
    position: absolute; top: 50px; width: 105px; height: 32px; border-radius: 2px;
    color: var(--white); font-size: 12px; font-weight: 700; letter-spacing: 0.6px;
    text-align: center; line-height: 32px; text-transform: uppercase;
  }
  .btn-signup { left: 883px; background: var(--signup-blue); }
  .btn-login { left: 996px; background: var(--login-green); }

  /* Intro */
  .step-title {
    position: absolute; left: 99px; top: 169px;
    font-size: 20px; font-weight: 700; color: var(--ink-dark); text-transform: uppercase;
  }
  .step-count { color: var(--accent-blue); margin-left: 24px; }
  .step-lead {
    position: absolute; left: 99px; top: 211px; width: 900px;
    font-size: 12px; font-weight: 600; line-height: 21px;
    color: var(--accent-orange); text-transform: uppercase;
  }
  .points { position: absolute; left: 99px; top: 267px; width: 1002px; list-style: none; }
  .points li {
    position: relative; padding-left: 19px; margin-bottom: 12px;
    font-size: 11px; font-weight: 300; line-height: 20px; color: var(--ink-body);
  }
  .points li svg { position: absolute; left: 0; top: 5px; }

  /* Connect cards */
  .connect-card {
    position: absolute; top: 460px; width: 238px; height: 55px;
    border-radius: 2px; color: var(--white);
    box-shadow: inset 0 -1px 0 rgba(0,0,0,0.2), 0 1px 1px rgba(0,0,0,0.15);
  }
  .card-chirply { left: 99px; background: linear-gradient(#47c6f1, #33b1e1); }
  .card-pictora { left: 354px; background: linear-gradient(#b4712f, #9c5c25); }
  .card-tunewave { left: 608px; background: linear-gradient(#9cbd42, #80a231); }
  .card-songbox { left: 863px; background: linear-gradient(#e24343, #cd2e2e); }
  .card-mark {
    position: absolute; left: 14px; top: 18px; width: 18px; height: 18px;
    border-radius: 50%; background: rgba(255,255,255,0.9);
  }
  .card-title { position: absolute; left: 47px; top: 12px; font-size: 13px; font-weight: 600; line-height: 16px; }
  .card-sub { position: absolute; left: 47px; top: 28px; font-size: 10.5px; font-weight: 300; line-height: 14px; }

  /* Status notes */
  .status-note {
    position: absolute; top: 529px; width: 143px; height: 32px; border-radius: 2px;
    color: var(--white); font-size: 13px; text-align: center; line-height: 32px;
    box-shadow: 0 1px 2px rgba(0,0,0,0.2);
  }
  .status-note::before {
    content: ""; position: absolute; left: 15px; top: -5px;
    border-left: 5px solid transparent; border-right: 5px solid transparent;
    border-bottom: 5px solid currentColor;
  }
  .note-linked { left: 99px; background: var(--note-green); }
  .note-linked::before { border-bottom-color: var(--note-green); }
  .note-unavailable { left: 609px; background: var(--note-red); }
  .note-unavailable::before { border-bottom-color: var(--note-red); }

  /* Footer */
  .site-footer {
    position: absolute; left: 0; top: 602px; width: 1200px; height: 62px;
    background: var(--footer-bg);
  }
  .copyright {
    position: absolute; left: 98px; top: 23px;
    font-size: 11px; color: var(--footer-ink);
  }
  .footer-links { position: absolute; left: 1036px; top: 22px; display: flex; gap: 8px; }
  .footer-links span { width: 16px; height: 16px; border-radius: 50%; background: var(--footer-ink); }
</style>
</head>
<body>
  <header class="site-header">
    <div class="brand">VENUEO</div>
    <div class="search">
      <div class="search-field">Search
        <svg width="10" height="10" viewBox="0 0 10 10" aria-hidden="true">
          <circle cx="4" cy="4" r="3" fill="none" stroke="#fff" stroke-width="1.4"/>
          <line x1="6.2" y1="6.2" x2="9" y2="9" stroke="#fff" stroke-width="1.6"/>
        </svg>
      </div>
    </div>
    <div class="header-btn btn-signup">Sign up</div>
    <div class="header-btn btn-login">Log in</div>
  </header>

  <main>
    <h1 class="step-title">Dignissimos ducimus qui blanditiis <span class="step-count">Step 1 0f 5</span></h1>
    <p class="step-lead">On the other hand, we denounce with righteous indignation and dislike men who are so beguiled and demoralized by the charms of pleasure of the moment, so blinded by desire</p>

    <ul class="points">
      <li><svg width="10" height="10" viewBox="0 0 10 10" aria-hidden="true"><circle cx="5" cy="5" r="4" fill="none" stroke="#3aa3c9" stroke-width="2" stroke-dasharray="1.6 1"/><circle cx="5" cy="5" r="2.4" fill="#3aa3c9"/><circle cx="5" cy="5" r="0.9" fill="#eff0f5"/></svg>Must explain to you how all this mistaken idea of denouncing pleasure and praising pain was born and I will give you a complete account of the system, and expound the actual teachings of the great explorer of the truth, the master-builder saying through shrinking from toil and pain......</li>
      <li><svg width="10" height="10" viewBox="0 0 10 10" aria-hidden="true"><circle cx="5" cy="5" r="4" fill="none" stroke="#3aa3c9" stroke-width="2" stroke-dasharray="1.6 1"/><circle cx="5" cy="5" r="2.4" fill="#3aa3c9"/><circle cx="5" cy="5" r="0.9" fill="#eff0f5"/></svg>Must explain to you how all this mistaken idea of denouncing pleasure and praising pain was born and I will give you a complete account of the system, and expound the actual teachings of the great explorer of the truth, the master-builder saying through shrinking from toil and pain......</li>
      <li><svg width="10" height="10" viewBox="0 0 10 10" aria-hidden="true"><circle cx="5" cy="5" r="4" fill="none" stroke="#3aa3c9" stroke-width="2" stroke-dasharray="1.6 1"/><circle cx="5" cy="5" r="2.4" fill="#3aa3c9"/><circle cx="5" cy="5" r="0.9" fill="#eff0f5"/></svg>Must explain to you how all this mistaken idea of denouncing pleasure and praising pain was born and I will give you a complete account of the system, and expound the actual teachings of the great explorer of the truth, the master-builder saying through shrinking from toil and pain......</li>
    </ul>

    <div class="connect-card card-chirply"><span class="card-mark"></span><div class="card-title">Follow on Chirply</div><div class="card-sub">Item updates via Chirply!</div></div>
    <div class="connect-card card-pictora"><span class="card-mark"></span><div class="card-title">Follow on Pictora</div><div class="card-sub">Find out about new items first!</div></div>
    <div class="connect-card card-tunewave"><span class="card-mark"></span><div class="card-title">Follow on Tunewave</div><div class="card-sub">Find out about new items first!</div></div>
    <div class="connect-card card-songbox"><span class="card-mark"></span><div class="card-title">watch on Songbox</div><div class="card-sub">Need help? Let’s get in touch!</div></div>

    <div class="status-note note-linked">successfully linked</div>
    <div class="status-note note-unavailable">Not available</div>
  </main>

  <footer class="site-footer">
    <p class="copyright">Copyrights@venueo.2015.Allrights Reserved.</p>
    <div class="footer-links"><span></span><span></span><span></span></div>
  </footer>
</body>
</html>
```